Web design project for exciting Australian start-up

Background
We are looking for a creative and talented web design artist to work alongside our market leading web developer.
• You will be required to create a modern and clean design theme for our website, incorporating selected rustic colour scheme elements for our exciting Australian start-up to operate within the coffee industry.
reoccurring work to be expected to flow to the successful designer.
Requirements
• c. 5 - 10 page website
• Landing page
• Log in/ out
• 404 template
• Typography is emphasised
• Please use either a) typemarrow.com, b) free web fonts, c) brindle fonts
• All design elements in vector format
• Preferably with icons for each header title(i.e. about us, how it works etc) but designer have free reign over how the site looks, so might not be applicable
• All pages to be responsive
• Down to eSlab resolution

High level visual design brief attached - additional pages to be worked from base design.

Design inspiration
• We would like to use design elements from the following sources:
http://www.zandrix.com/halcyon/ (Functionality)
Colour scheme refer to logo and complementary style guide

```html
<!DOCTYPE html>
<html lang="en"><head><meta charset="utf-8"><title>Bean Orbit – Dashboard</title>
<link href="https://fonts.googleapis.com/css2?family=Roboto:wght@300;400;500;700&family=Roboto+Condensed:wght@300;400&display=swap" rel="stylesheet">
<style>
:root{--orange:#f9a54b;--orange-text:#f7941d;--dark:#4a4a4b;--panel:#f2f2f2;--line:#e2e2e2;--muted:#9a9a9a;--text:#333;--footer:#e9e9e9}
*{box-sizing:border-box;margin:0;padding:0}
html,body{width:1200px;height:1016px;overflow:hidden;background:#fff;font-family:"Roboto",Arial,sans-serif;color:var(--text);font-weight:300}
.abs{position:absolute}
.header{position:absolute;left:0;top:0;width:1200px;height:84px;border-bottom:1px solid var(--line)}
.brand{position:absolute;left:51px;top:23px;display:flex;align-items:center;gap:8px;font-weight:700;font-size:22px;letter-spacing:1px;color:#333}
.brand .dot{width:34px;height:34px;border-radius:50%;background:var(--orange)}
.nav{position:absolute;right:52px;top:28px;display:flex;align-items:center;gap:25px;font-size:12px;color:#666;font-weight:400}
.nav .logout{background:var(--dark);color:#fff;padding:7px 10px;border-radius:2px;display:flex;gap:6px;align-items:center}
.bar{height:35px;display:flex;align-items:center;padding:0 9px;gap:7px;font-size:15px;font-weight:400}
.bar.orange{background:var(--orange);color:#222}
.bar.dark{background:var(--dark);color:#fff}
.col-left{left:51px;top:102px;width:275px}
.col-mid{left:338px;top:102px;width:523px}
.col-right{left:873px;top:102px;width:275px}
.photo{height:202px;background:radial-gradient(ellipse at 50% 45%,#fff 0,#eee 35%,#d9d9d9 60%,#f0f0f0 75%);}
.arrows{margin-left:auto;display:flex;gap:5px}
.arrows span{width:22px;height:22px;background:var(--dark);color:#fff;font-size:12px;display:flex;align-items:center;justify-content:center}
.caption{height:38px;background:var(--panel);display:flex;align-items:center;justify-content:space-between;padding:0 8px;border-bottom:1px solid var(--line)}
.caption .name{color:var(--orange-text);font-size:14px;font-weight:400}
.caption .date{font-size:13px;color:#666;display:flex;gap:5px;align-items:center}
.location{height:69px;background:#fff;border:1px solid var(--line);border-top:0;padding:15px 7px;font-size:13px;line-height:20px;color:#222;font-weight:400}
.account{margin-top:27px}
.acc-item{background:var(--panel);border-bottom:1px solid var(--line);padding:15px 8px;height:86px}
.acc-item h4{font-size:15px;font-weight:400;color:#333;margin-bottom:10px}
.acc-item p{font-size:13px;color:var(--muted)}
.title-big{font-family:"Roboto Condensed",sans-serif;font-size:23px;font-weight:300;height:37px;padding:0 10px;display:flex;align-items:center}
.title-big.dark{background:var(--dark);color:var(--orange)}
.title-big.orange{background:var(--orange);color:#222}
.tri{display:inline-block;width:0;height:0;border-left:5px solid transparent;border-right:5px solid transparent;border-top:7px solid #999;margin-right:8px}
.filter{height:38px;display:flex;align-items:center;padding-left:2px;font-size:13.5px;color:#444;border-bottom:1px dotted #ddd}
.tender{padding:18px 1px;height:82px;border-bottom:1px solid var(--line)}
.time{color:var(--orange-text);font-size:13.5px;font-weight:400;margin-bottom:8px}
.small{font-size:12.5px;color:#777;line-height:16px}
.purchases{margin-top:22px}
table{width:523px;border-collapse:collapse;font-size:13px;color:var(--muted)}
th{height:49px;text-align:left;font-weight:400;color:#444;padding-left:10px;border:1px solid var(--line);border-top:0;font-size:13.5px}
td{height:40.7px;padding-left:10px;border:1px solid var(--line)}
tr:nth-child(odd) td{background:var(--panel)}
.inbox-list{background:var(--panel);padding:16px 9px;height:76px;font-size:13.5px;color:#888;line-height:27px}
.week{height:42px;display:flex;align-items:center;justify-content:space-between;padding:0 10px;font-size:15px;color:#333;font-weight:400;border-bottom:1px solid var(--line)}
.deliv{background:var(--panel);height:163px;position:relative}
.deliv .item{padding:11px 8px;height:71px;border-bottom:1px solid #fff;margin-right:10px}
.scroll{position:absolute;right:2px;top:4px;width:8px;height:155px;border:1px solid #ccc;background:#fff}
.cal-wrap{background:var(--panel);padding-top:25px;height:370px}
.cal-head{height:42px;background:linear-gradient(#7a7a7a,#5a5a5a);color:#fff;display:flex;align-items:center;justify-content:space-between;padding:0 20px;font-size:15.5px;font-weight:400}
.cal-head span.a{color:#aaa;font-size:11px}
.cal{display:grid;grid-template-columns:repeat(7,1fr);background:#ccc;gap:1px;border:1px solid #ccc;border-top:0}
.cal div{height:38.5px;background:linear-gradient(#fafafa,#e4e4e4);display:flex;align-items:center;justify-content:center;font-size:15px;font-weight:500;color:#333}
.cal .wd{background:#e6e6e6;color:#aaa;font-weight:400;height:37px}
.cal .off{color:#aaa;font-weight:400}
.cal .sel{background:var(--orange);color:#fff}
.download{padding:16px 8px;display:flex;align-items:center;gap:7px;color:var(--orange-text);font-size:15px;font-weight:400}
.footer{position:absolute;left:0;top:817px;width:1200px;height:199px;background:var(--footer)}
.footer h5{font-size:13px;font-weight:400;color:#111;margin-bottom:17px}
.footer .col{position:absolute;top:34px;font-size:12.5px;color:#333;line-height:20px}
.footer .about p{font-size:11.3px;color:#555;line-height:16.6px;width:305px}
.social li{list-style:none;display:flex;align-items:center;gap:8px;margin-bottom:7px;font-size:13.5px}
.social i{width:17px;height:17px;border-radius:50%;background:#777;display:inline-block}
.fbrand{position:absolute;left:962px;top:53px;display:flex;align-items:center;gap:6px;font-weight:700;font-size:19px;letter-spacing:1px;color:#555}
.fbrand .dot{width:30px;height:30px;border-radius:50%;background:#999}
.copy{position:absolute;left:962px;top:110px;font-size:12.5px;color:#333}
</style></head><body>
<header class="header">
  <div class="brand"><span class="dot"></span>BEAN ORBIT</div>
  <nav class="nav"><span>HOME</span><span>ABOUT US</span><span>MARKETPLACE</span><span>LOGGED IN</span>
    <span class="logout"><svg width="16" height="12" viewBox="0 0 16 12"><circle cx="6" cy="6" r="5" fill="none" stroke="#fff" stroke-width="1.6"/><path d="M6 6h9M12 3l3 3-3 3" stroke="#fff" stroke-width="1.6" fill="none"/></svg>LOGOUT</span></nav>
</header>

<section class="abs col-left">
  <div class="bar orange"><svg width="16" height="14"><rect x="1" y="1" width="12" height="10" fill="none" stroke="#333" stroke-width="1.4"/><rect x="4" y="4" width="11" height="9" fill="none" stroke="#333" stroke-width="1.4"/></svg>Photos<div class="arrows"><span>&#8249;</span><span>&#8250;</span></div></div>
  <div class="photo" role="img" aria-label="Photo of a chocolate dessert on a white plate"></div>
  <div class="caption"><span class="name">CAFE MERROW</span><span class="date"><svg width="18" height="18"><rect x="1" y="3" width="16" height="14" fill="none" stroke="#777" stroke-width="1.3"/><line x1="1" y1="7" x2="17" y2="7" stroke="#777"/><text x="9" y="15" font-size="8" text-anchor="middle" fill="#777">10</text></svg>Feb,2014</span></div>
  <div class="location">Melbourne, Australia<br>Member Since [Feb,2014]</div>
  <div class="account">
    <div class="bar dark"><svg width="20" height="18"><circle cx="8" cy="5" r="4" fill="#fff"/><path d="M1 17c0-6 14-6 14 0z" fill="#fff"/><circle cx="16" cy="14" r="3" fill="none" stroke="#fff" stroke-width="1.5"/></svg>My Account</div>
    <div class="acc-item"><h4>Email Address</h4><p>...Verified</p></div>
    <div class="acc-item"><h4>Cafe Type</h4><p>(i.e. Cafe,speciality coffee shop,restaurant)</p></div>
    <div class="acc-item" style="height:75px"><h4>Cafe Type</h4><p>Verified</p></div>
  </div>
</section>

<section class="abs col-mid">
  <div class="title-big dark">Live Tenders</div>
  <div class="filter"><span class="tri"></span>Time remaining</div>
  <div class="tender"><div class="time">8 am - 11 am</div><div class="small">Delivery of order 3220x&nbsp; Order: 20kg Harbour Beans</div></div>
  <div class="purchases">
    <div class="title-big orange">Purchases</div>
    <table>
      <tr><th style="width:195px"><span class="tri"></span>All</th><th style="width:156px"><span class="tri"></span>Period (x months)</th><th><span class="tri"></span>A waiting feedback (x)</th></tr>
      <tr><td>Lorem ipsum dolor sit amet</td><td>dd/mm/yyyy</td><td>10,Feb ,2014</td></tr>
      <tr><td>Lorem ipsum dolor sit amet</td><td>dd/mm/yyyy</td><td>10,Feb ,2014</td></tr>
      <tr><td>Lorem ipsum dolor sit amet</td><td>dd/mm/yyyy</td><td>10,Feb ,2014</td></tr>
      <tr><td>Lorem ipsum dolor sit amet</td><td>dd/mm/yyyy</td><td>10,Feb ,2014</td></tr>
      <tr><td>Lorem ipsum dolor sit amet</td><td>dd/mm/yyyy</td><td>10,Feb ,2014</td></tr>
      <tr><td>Lorem ipsum dolor sit amet</td><td>dd/mm/yyyy</td><td>10,Feb ,2014</td></tr>
      <tr><td>Lorem ipsum dolor sit amet</td><td>dd/mm/yyyy</td><td>10,Feb ,2014</td></tr>
      <tr><td>Lorem ipsum dolor sit amet</td><td>dd/mm/yyyy</td><td>10,Feb ,2014</td></tr>
      <tr><td>Lorem ipsum dolor sit amet</td><td>dd/mm/yyyy</td><td>10,Feb ,2014</td></tr>
      <tr><td>Lorem ipsum dolor sit amet</td><td>dd/mm/yyyy</td><td>10,Feb ,2014</td></tr>
    </table>
  </div>
</section>

<section class="abs col-right">
  <div class="bar orange"><svg width="18" height="16"><path d="M2 7h14v8H2z" fill="none" stroke="#222" stroke-width="1.5"/><path d="M2 7l7 5 7-5M5 7V2h8v5" fill="none" stroke="#222" stroke-width="1.5"/></svg>Inbox</div>
  <div class="inbox-list"><div><span class="tri"></span>Messages</div><div><span class="tri"></span>Saved Searches</div></div>
  <div class="week"><span style="font-size:11px;color:#555">&#9664;</span>Incoming Deliveries this week<span style="font-size:11px;color:#555">&#9654;</span></div>
  <div class="deliv">
    <div class="item"><div class="time" style="margin-bottom:4px">8 am - 11 am</div><div class="small">Delivery of order 3220x<br>Order: 20kg Harbour Beans</div></div>
    <div class="item"><div class="time" style="margin-bottom:4px">8 am - 11 am</div><div class="small">Delivery of order 3220x<br>Order: 20kg Harbour Beans</div></div>
    <div class="scroll"></div>
  </div>
  <div class="cal-wrap">
    <div class="cal-head"><span class="a">&#9664;</span>Novembre 2014<span class="a">&#9654;</span></div>
    <div class="cal">
      <div class="wd">M</div><div class="wd">T</div><div class="wd">W</div><div class="wd">T</div><div class="wd">F</div><div class="wd">S</div><div class="wd">S</div>
      <div class="off">28</div><div>1</div><div>2</div><div>3</div><div class="sel">4</div><div>5</div><div>6</div>
      <div>7</div><div>8</div><div>9</div><div>10</div><div>11</div><div>12</div><div>13</div>
      <div>14</div><div>15</div><div>16</div><div>17</div><div>18</div><div>19</div><div>20</div>
      <div>21</div><div>22</div><div>23</div><div>24</div><div>25</div><div>26</div><div>27</div>
      <div>28</div><div>29</div><div>30</div><div>31</div><div class="off">1</div><div class="off">2</div><div class="off">3</div>
    </div>
    <div class="download"><svg width="18" height="18"><circle cx="9" cy="9" r="7.5" fill="none" stroke="#333" stroke-width="1.5"/><path d="M9 4v8M6 9l3 3 3-3" fill="none" stroke="#333" stroke-width="1.5"/></svg>Download</div>
  </div>
</section>

<footer class="footer">
  <div class="col about" style="left:51px"><h5>ABOUT US</h5><p>Lorem ipsum dolor sit amet, consectetur adipisicing elit, sed do eiusmod tempor incididunt ut labore et dolore magna aliqua. Ut enim ad minim veniam, quis nostrud exercitation ullamco laboris nisi ut aliquip ex ea commodo consequat. Duis aute irure dolor in reprehenderit in voluptate velit esse cillum dolore eu fugiat nulla pariatur.</p></div>
  <div class="col" style="left:429px"><h5>HELPFUL INFO</h5>About us<br>Media Enquiries<br>Terms &amp; Conditions<br>Privacy Policy</div>
  <div class="col" style="left:618px"><h5>WHO WE ARE</h5>How It Works<br>Faq<br>Contact Us</div>
  <div class="col" style="left:788px"><h5>FOLLOW US</h5><ul class="social"><li><i></i>Chatterly</li><li><i></i>Linkwork</li><li><i></i>Chatterly</li><li><i></i>Linkwork</li></ul></div>
  <div class="fbrand"><span class="dot"></span>BEAN ORBIT</div>
  <div class="copy">Copyright © 2014 Bean Orbit.</div>
</footer>
</body></html>
```